Brightfield Ventures Inc. Letterhead

Creation of attractive and eye catching letterhead for a business start-up for the construction industry. Letterhead must relate to construction, but avoid standard hammer and tools in the design.

I forgot to add some details, sorry about that. Some pertinent info: Ph: 916-555-0187 brightfieldventures.example 448 Willowmere Ave, Ste 210 Folsom, CA 95999 info@brightfieldventures.example not sure if slogan should be in there" “Connecting construction professionals to create a purpose driven industry.” must be able to be used in word. Thanks!

```html
<!DOCTYPE html>
<html lang="en">
<head>
<meta charset="utf-8">
<title>Brightfield Ventures Inc. Letterhead</title>
<link rel="stylesheet" href="https://fonts.googleapis.com/css2?family=Lato:wght@400;700&family=Yellowtail&display=swap">
<style>
  :root {
    --navy: #1c1f5a;
    --red: #c8202c;
    --body-text: #4a4a4f;
    --paper: #ffffff;
    --rule: #9a9aa2;
  }
  * { margin: 0; padding: 0; box-sizing: border-box; }
  html, body { width: 869px; height: 1200px; overflow: hidden; background: var(--paper); }
  .letterhead {
    position: relative;
    width: 869px;
    height: 1200px;
    background: var(--paper);
    font-family: "Lato", Arial, sans-serif;
    color: var(--body-text);
  }
  .brand {
    position: absolute;
    left: 74px;
    top: 88px;
    display: flex;
    align-items: center;
    gap: 12px;
  }
  .brand-mark {
    width: 16px;
    height: 16px;
    background: var(--red);
  }
  .brand-name {
    font-weight: 700;
    font-size: 19px;
    letter-spacing: 1.6px;
    text-transform: uppercase;
    color: var(--navy);
  }
  .contact {
    position: absolute;
    left: 608px;
    top: 58px;
    padding-left: 10px;
    border-left: 1px solid var(--rule);
    font-size: 12.5px;
    line-height: 19px;
    color: #3a3a40;
    list-style: none;
  }
  .contact li { display: flex; align-items: center; gap: 4px; white-space: nowrap; }
  .icon { width: 10px; height: 10px; fill: var(--red); flex: none; }
  .salutation {
    position: absolute;
    left: 74px;
    top: 231px;
    font-weight: 700;
    font-size: 16.5px;
    color: var(--navy);
  }
  .body-copy {
    position: absolute;
    left: 74px;
    top: 275px;
    width: 722px;
  }
  .body-copy p {
    font-size: 16.4px;
    line-height: 27px;
    text-align: justify;
    margin-bottom: 22px;
  }
  .closing {
    position: absolute;
    left: 76px;
    top: 759px;
    font-size: 19px;
    color: #2a2a30;
  }
  .signature {
    position: absolute;
    left: 76px;
    top: 792px;
    font-family: "Yellowtail", cursive;
    font-size: 34px;
    color: var(--navy);
  }
  .address {
    position: absolute;
    left: 0;
    right: 0;
    top: 1168px;
    display: flex;
    justify-content: center;
    align-items: center;
    gap: 4px;
    font-size: 12.5px;
    color: #3a3a40;
  }
</style>
</head>
<body>
<main class="letterhead">
  <header>
    <div class="brand">
      <span class="brand-mark"></span>
      <span class="brand-name">Brightfield Ventures Inc.</span>
    </div>
    <ul class="contact">
      <li><svg class="icon" viewBox="0 0 10 10"><path d="M2 0.5l1.6 2.3-0.9 1a5 5 0 0 0 2.6 2.6l1-0.9 2.3 1.6-0.8 1.9C5 9.3 0.7 5 0.1 1.3z"/></svg>916-555-0187</li>
      <li><svg class="icon" viewBox="0 0 10 10"><path d="M0 2h10v6H0z M0.5 2.2L5 5.6l4.5-3.4" stroke="#fff" stroke-width="0.8"/></svg>info@brightfieldventures.example</li>
      <li><svg class="icon" viewBox="0 0 10 10"><circle cx="5" cy="5" r="4.6"/><path d="M0.6 5h8.8M5 0.5v9M2 2.3h6M2 7.7h6" stroke="#fff" stroke-width="0.6" fill="none"/></svg>www.brightfieldventures.example</li>
    </ul>
  </header>

  <p class="salutation">Dear Mr. Lorem,</p>

  <section class="body-copy">
    <p>Lorem ipsum dolor sit amet, consectetuer adipiscing elit, sed diam nonummy nibh euismod tincidunt ut laoreet dolore magna aliquam erat volutpat. Ut wisi enim ad minim veniam, quis nostrud exerci tation ullamcorper suscipit lobortis nisl ut aliquip ex ea commodo consequat. Duis autem vel eum iriure dolor in hendiusto odio dignissim qui blandit praesent luptatum zzril delenit augue duis dolore te feugait nulla facilisi.</p>
    <p>Lorem ipsum dolor sit amet, consectetuer adipiscing elit, sed diam nonummy nibh euismod tincidunt ut laoreet dolore magna aliquam erat volutpat. Ut wisi enim ad minim veniam, quis nostrud exerci tation ullamcorper suscipit lobortis nisl ut aliquip ex ea commodo consequat. Duis autem vel eum iriure dolor in hendiusto odio dignissim qui blandit praesent luptatum zzril delenit augue duis dolore te feugait nulla facilisi.</p>
    <p>Lorem ipsum dolor sit amet, consectetuer adipiscing elit, sed diam nonummy nibh euismod tincidunt ut laoreet dolore magna aliquam erat volutpat. Ut wisi enim ad minim veniam, quis nostrud exerci tation ullamcorper suscipit lobortis nisl ut aliquip ex ea commodo consequat. Duis autem vel eum iriure dolor in hendiusto odio dignissim qui blandit praesent luptatum zzril delenit augue duis dolore te feugait nulla facilisi.</p>
  </section>

  <p class="closing">Sincerely Your,</p>
  <p class="signature">Your Name</p>

  <footer class="address">
    <svg class="icon" viewBox="0 0 10 10"><circle cx="5" cy="5" r="4.5"/><circle cx="5" cy="5" r="1.8" fill="#fff"/></svg>
    448 Willowmere Ave, Ste 210, Folsom, CA 95999
  </footer>
</main>
</body>
</html>
```